I need to create a product box

I need a designer for a candle-making kit. Attached please find the die-cut and some of the elements I will like to include in the box. Also, there is a sample box. I want the designer to know this is an ecofriendly product but the packaging needs to be classy, unisex and eye-catching.

file:///C:/Users/mauro/Downloads/Untitled%20design.svg

Colors
0054AA
0677BA
7BADD7
CADEEF
E8F1F8
0094D4
00A9DD
6FCCEA
C7EBF8
E9F6FB
00AB8E
00BBA5
67D7C9
C6EFE9
E9F9F6
FFF300
FFF600
FEFA6F
FFFEC7
FFFEE8
FFC000
F8CF3A
FAE287
FDF2CF
FEFAEE
F0912C
F2A743
F7CA91
FBE8D2
FDF5EE
A7469A
B969AE
D3A5CF
EDDBEB
F8F0F9

```html
<!DOCTYPE html>
<html lang="en">
<head>
<meta charset="utf-8">
<title>Wickwood – Candle Making Kit Dieline</title>
<link rel="stylesheet" href="https://fonts.googleapis.com/css2?family=Great+Vibes&family=Cormorant+Garamond:wght@500;600&family=Quicksand:wght@300;400&family=Roboto+Condensed:wght@400;700&family=Montserrat:wght@400;600&display=swap">
<style>
  :root{
    --backdrop:#dcc6df;
    --board:#f1e8e9;
    --cut-line:#c7a8c5;
    --fold-line:#d8c8d2;
    --forest:#617a60;
    --forest-ink:#5a735a;
    --plum:#a7469a;
    --lilac-frame:#d9cde0;
    --warning-ink:#4a4a4a;
    --white:#ffffff;
  }
  *{box-sizing:border-box;margin:0;padding:0}
  html,body{width:1200px;height:1200px;overflow:hidden;background:var(--backdrop)}
  .sheet{position:relative;width:1200px;height:1200px}
  .dieline{position:absolute;inset:0}
  .abs{position:absolute}

  .script-line{font-family:"Great Vibes",cursive;color:var(--forest-ink);font-size:22px;white-space:nowrap;transform:rotate(180deg);text-align:center}

  .info-frame{position:absolute;border:3px solid var(--lilac-frame);background:var(--board)}
  .warning{font-family:"Roboto Condensed",sans-serif;color:var(--warning-ink);margin-bottom:9px}
  .warning h4{font-size:6.5px;font-weight:700;margin-bottom:2px}
  .warning h4::before{content:"⚠ ";font-size:6px}
  .warning p{font-size:4.3px;line-height:1.3;text-align:justify}

  .kit-title{font-family:"Quicksand",sans-serif;font-weight:300;color:var(--plum);font-size:12.5px;margin-bottom:8px}
  .kit-list{font-family:"Quicksand",sans-serif;color:var(--plum);font-size:5.6px;list-style:none;line-height:8.5px}
  .kit-list span{display:inline-block;width:10px}

  .brand{position:absolute;text-align:center;color:var(--forest-ink)}
  .brand-name{font-family:"Cormorant Garamond",serif;font-weight:600;font-size:24px;letter-spacing:.5px;white-space:nowrap}
  .brand-mark{display:block;width:9px;height:9px;border-radius:50%;background:var(--forest-ink);margin:0 auto 4px}
  .brand-tag{font-family:"Cormorant Garamond",serif;font-weight:600;font-size:4.6px;letter-spacing:1.3px;white-space:nowrap}

  .web-url{font-family:"Montserrat",sans-serif;color:var(--white);font-size:8.5px;transform:rotate(90deg);transform-origin:left top;white-space:nowrap}
  .paraben{font-family:"Montserrat",sans-serif;color:var(--white);transform:rotate(90deg);transform-origin:left top;white-space:nowrap;line-height:1}
  .paraben .small{font-size:6px;letter-spacing:.5px;display:block}
  .paraben .big{font-size:10px;font-weight:400;display:block}
</style>
</head>
<body>
<div class="sheet">

  <svg class="dieline" width="1200" height="1200" viewBox="0 0 1200 1200">
    <!-- board pieces -->
    <rect x="321" y="117" width="558" height="178" fill="var(--board)" stroke="var(--cut-line)" stroke-width=".8"/>
    <rect x="66" y="295" width="1067" height="235" fill="var(--board)" stroke="var(--cut-line)" stroke-width=".8"/>
    <rect x="57" y="388" width="9" height="56" fill="var(--forest)"/>
    <rect x="1133" y="388" width="10" height="56" fill="var(--forest)"/>
    <rect x="321" y="530" width="558" height="178" fill="var(--board)" stroke="var(--cut-line)" stroke-width=".8"/>
    <rect x="259" y="708" width="682" height="234" rx="50" fill="var(--board)" stroke="var(--cut-line)" stroke-width=".8"/>
    <path d="M340 948 L425 942 L775 942 L860 948 Q879 952 879 970 L879 1050 Q879 1070 860 1080 L775 1122 L425 1122 L340 1080 Q321 1070 321 1050 L321 970 Q321 952 340 948 Z" fill="var(--board)" stroke="var(--cut-line)" stroke-width=".8"/>

    <!-- green side panels -->
    <rect x="245" y="295" width="180" height="235" fill="var(--forest)"/>
    <rect x="775" y="295" width="180" height="235" fill="var(--forest)"/>
    <rect x="425" y="388" width="9" height="56" fill="var(--forest)"/>
    <rect x="766" y="388" width="9" height="56" fill="var(--forest)"/>

    <!-- fold lines -->
    <g stroke="var(--fold-line)" stroke-width=".8" fill="none">
      <line x1="425" y1="117" x2="425" y2="1122"/>
      <line x1="775" y1="117" x2="775" y2="1122"/>
      <line x1="321" y1="295" x2="879" y2="295"/>
      <line x1="321" y1="530" x2="879" y2="530"/>
      <line x1="321" y1="708" x2="879" y2="708"/>
      <line x1="425" y1="942" x2="775" y2="942" stroke="#a9c4a6"/>
    </g>

    <!-- heart on top flap -->
    <path class="heart-icon" d="M600 256 C592 250 590 246 590 243 C590 239 594 237 597 239 L600 241 L603 239 C606 237 610 239 610 243 C610 246 608 250 600 256 Z" fill="var(--forest-ink)"/>

    <!-- faint floral accents on inner panel -->
    <g role="img" aria-label="Faint lilac line-drawn flowers in the panel corners" fill="#e2d6e6" opacity=".8">
      <circle cx="456" cy="319" r="11"/>
      <circle cx="676" cy="319" r="11"/>
      <circle cx="437" cy="514" r="8"/>
      <circle cx="638" cy="516" r="10"/>
    </g>

    <!-- left green panel florals -->
    <g role="img" aria-label="Pastel line-drawn flowers and a leaf on the green side panel" opacity=".75">
      <circle cx="272" cy="329" r="16" fill="#d3a5cf"/>
      <ellipse cx="295" cy="326" rx="14" ry="8" fill="#67d7c9" opacity=".6"/>
      <circle cx="252" cy="422" r="10" fill="#b969ae" opacity=".7"/>
      <circle cx="274" cy="485" r="17" fill="#7badd7"/>
      <circle cx="376" cy="512" r="18" fill="#fae287"/>
    </g>

    <!-- right green panel florals -->
    <g role="img" aria-label="Pastel line-drawn flowers and leaves on the green side panel" opacity=".75">
      <circle cx="817" cy="329" r="17" fill="#7badd7"/>
      <circle cx="802" cy="348" r="13" fill="#fefa6f" opacity=".6"/>
      <circle cx="902" cy="348" r="16" fill="#f7a1a1"/>
      <circle cx="810" cy="400" r="19" fill="#b969ae"/>
      <ellipse cx="887" cy="412" rx="42" ry="14" fill="#c6efe9" opacity=".55" transform="rotate(15 887 412)"/>
      <circle cx="920" cy="430" r="20" fill="#fae287"/>
      <circle cx="808" cy="497" r="22" fill="#eddbeb"/>
      <ellipse cx="830" cy="508" rx="8" ry="18" fill="#67d7c9" opacity=".6"/>
      <circle cx="923" cy="494" r="19" fill="#cadeef"/>
    </g>

    <!-- badges -->
    <g fill="var(--white)">
      <polygon points="332,364 351,375 351,397 332,408 313,397 313,375"/>
      <circle cx="332" cy="428" r="21"/>
      <circle cx="332" cy="475" r="21"/>
    </g>

    <!-- front panel illustration -->
    <rect x="428" y="712" width="195" height="228" fill="url(#spa-left)" role="img" aria-label="Line illustration of bamboo, orchid, stacked stones, a floating candle and pastel flowers"/>
    <rect x="612" y="800" width="163" height="120" fill="url(#spa-right)" role="img" aria-label="Pastel line-drawn flowers in green, pink, lilac and blue"/>

    <!-- lower flap illustration -->
    <rect x="425" y="944" width="130" height="164" fill="url(#spa-flap)" role="img" aria-label="Line illustration of orchid, stones and a floating candle"/>
    <rect x="648" y="955" width="125" height="110" fill="url(#spa-right)" role="img" aria-label="Pastel line-drawn flowers in pink, yellow and blue"/>

    <defs>
      <linearGradient id="spa-left" x1="0" y1="0" x2="1" y2="1">
        <stop offset="0" stop-color="#f4e3ec"/>
        <stop offset=".45" stop-color="#dfe6dc"/>
        <stop offset="1" stop-color="#e6e3f0"/>
      </linearGradient>
      <linearGradient id="spa-right" x1="0" y1="0" x2="1" y2="1">
        <stop offset="0" stop-color="#e4f0dd"/>
        <stop offset=".5" stop-color="#f6dde4"/>
        <stop offset="1" stop-color="#e1e0f3"/>
      </linearGradient>
      <linearGradient id="spa-flap" x1="0" y1="0" x2="1" y2="1">
        <stop offset="0" stop-color="#dde5da"/>
        <stop offset="1" stop-color="#ece9e6"/>
      </linearGradient>
    </defs>
  </svg>

  <!-- top flap messages -->
  <div class="abs script-line" style="left:425px;top:172px;width:350px">Hope this kit can help you light up your path to happiness</div>
  <div class="abs script-line" style="left:425px;top:196px;width:350px">When everything seemed dark I lit up a candle</div>

  <!-- bottom panel message -->
  <div class="abs script-line" style="left:425px;top:605px;width:350px">When everything seemed dark I lit up a candle</div>

  <!-- safety information -->
  <div class="info-frame" style="left:442px;top:338px;width:193px;height:165px;padding:14px 10px 8px 10px">
    <div class="warning">
      <h4>WARNING:</h4>
      <p>Burn within sight. Keep away from things that catch fire, children and pets. Never leave burning candles unattended. Trim wick to 1/4 in before each use.</p>
    </div>
    <div class="warning">
      <h4>WARNING:</h4>
      <p>DO NOT MICROWAVE. DO NOT EXCEED THE WAX TEMPERATURE LISTED. If wax catches fire, smother with a lid. Never use water.</p>
    </div>
    <div class="warning">
      <h4>AVERTISSEMENT:</h4>
      <p>Brûler à portée de vue. Tenir hors de portée des enfants et des animaux. Ne jamais laisser une bougie allumée sans surveillance.</p>
    </div>
    <div class="warning">
      <h4>AVERTISSEMENT:</h4>
      <p>NE PAS PASSER AU MICRO-ONDES. NE PAS DÉPASSER LA TEMPÉRATURE INDIQUÉE. Si la cire prend feu, étouffer avec un couvercle.</p>
    </div>
  </div>

  <!-- kit contents -->
  <div class="info-frame" style="left:644px;top:338px;width:112px;height:165px;padding:10px 8px 8px 10px">
    <div class="kit-title">DYI Candle Set</div>
    <ol class="kit-list">
      <li><span>1.</span>7 Bags of soy wax (8 oz each)</li>
      <li><span>2.</span>4 Glass Jars (7 cm)</li>
      <li><span>3.</span>3 Black tin cans (8 oz each)</li>
      <li><span>4.</span>20 Decorative labels</li>
      <li><span>5.</span>3 Bags of dry flowers</li>
      <li><span>6.</span>2 Gift labels</li>
      <li><span>7.</span>3 Centering devices</li>
      <li><span>8.</span>7 Fragrance oil (10ml each)</li>
      <li><span>9.</span>1 Digital thermometer</li>
      <li><span>10.</span>1 mixing spoon</li>
      <li><span>11.</span>Candle wick</li>
      <li><span>12.</span>10 Glue dots</li>
      <li><span>13.</span>10 Color dye</li>
      <li><span>14.</span>1 Melting pot</li>
    </ol>
  </div>

  <!-- left side panel text -->
  <div class="abs paraben" style="left:332px;top:324px">
    <span class="small">PARABEN</span>
    <span class="big">FREE</span>
  </div>
  <div class="abs web-url" style="left:276px;top:366px">www.wickwoodstudio.com</div>

  <!-- front panel brand -->
  <div class="brand" style="left:622px;top:738px;width:126px">
    <span class="brand-mark"></span>
    <div class="brand-name">Wickwood</div>
    <div class="brand-tag">LUXURY CANDLE MAKING KIT</div>
  </div>

  <!-- lower flap brand -->
  <div class="brand" style="left:537px;top:1006px;width:126px">
    <span class="brand-mark"></span>
    <div class="brand-name">Wickwood</div>
    <div class="brand-tag">LUXURY CANDLE MAKING KIT</div>
  </div>

</div>
</body>
</html>
```